Wordpress Theme for Medical Clinics

** Please view updated Sitemap2.pdf doc to clarify some confusion ***

This is a multiuser WordPress subscription site for medical clinics. Please see attachment for sitemap. Please do not include extra content like social media icons, search bars, or images. If you have questions, please ask for clarification.
The site contains the following pages and sub-pages:

1. Home
2. Our Clinic
2a. Our Clinic > Mission
2b. Our Clinic > Services
2c. Our Clinic > Clinic Policies
2d. Our Clinic > Schedules
3. Our Staff
3a. Our Staff > [Staff member page]
4. Resources
4a. Resources > Patient Health (index)
4b. Resources > Patient Health (index) > [post]
4c. Resources > Links
4d. Resources > Forms
5. Alerts
5a. Alerts > [Alert Page]
6. Contact Us

Includes the Following Pages, Subpages, and Content
1. Home
a. About Us
b. Our Staff
c. Bulletins
d. Accepting New Patients (shown as an alert widget)
e. Links
i. Physician Toolbox
ii. Book an Appointment
f. Clinic Policies
i. Show first 3 policies (e.g. Late Arrivals, Missed Appointments, Fees)
ii. Link to Clinic Policies page
g. Primary widget (displayed on all pages)
i. Hours of operation
ii. Contact Info
1. Tel
2. Fax
3. Email
4. Address
5. Get directions (link to Google Maps)
2. Our Clinic
a. Main Page
i. Clinic Name
ii. Overview
iii. Languages Spoken
iv. Secondary Navigation
1. Mission
2. Services
3. Clinic Policies
4. Schedules (see attachment)
b. Our Clinic > Mission
c. Our Clinic > Services
i. For each service include service TITLE and DESCRIPTION
d. Our Clinic > Clinic Policies
i. For each policy include policy TITLE and DESCRIPTION
ii. Include the following policies in mockup
1. Late arrivals
2. Missed appointments
3. Fees for missed appointments
4. Referrals and follow-ups
5. Services not covered by RDA
6. Information for LTF patients
7. Medical Legal Reports
e. Our Clinic > Schedules
3. Our Staff
a. Main Page
i. Display a list of staff members. Include NAME and DESIGNATION
b. Our Staff > [Staff Name]
i. Include NAME, PICTURE, DESIGNATION, and BIO
4. Resources
a. Resources > Patient Health
i. Main Page
1. Posts (ordered by date)
a. Title
b. Summary
2. Side Navigation
a. Post Categories
ii. Patient Health > [post title]
1. Title
2. Post Category
3. Date
4. Author
5. Summary
6. Body
b. Resources > Links
1. Secondary Navigation - Categories
a. Sample Categories:
i. Local Services
ii. RDA and Drug Coverage
iii. Mental Health Resources
2. Category page
a. Include the following links in the 'Local Services' category
i. Hypertension clinics
ii. Home Care services
iii. Vaccine Clinics
c. Resources > Forms
i. Display a table with form TITLE and CATEGORY
ii. Side Navigation
1. Form Categories
a. Use the following sample Categories
i. Referrals
ii. Insurance
iii. Intake
iv. Discharge
v. Waivers
5. Alerts
a. Main page
i. List of all Alert posts
1. Include post TITLE as a link to the post
ii. Side Navigation
1. Alerts Archive
a. shown as Month + Number of posts
iii. Alerts > [Alert page]
1. Include TITLE, DATE, AUTHOR, BODY
6. Contact Us
a. Map
b. Hours of operation
c. Address
d. Phone number
e. Fax number
e. Fax number
f. Map
g. Email

Design notes:
- fixed width
- responsive (need designs for mobile, tablet, and desktop)
- simple, dark font, white background
- use Font Awesome icons where needed
- user adds own logo

Target Market(s)

Medical Clinics

Industry/Entity Type

Medical

Number of Pages Required

5+ page

Font styles to use
Serif
Sans Serif

Requirements
Must have
• Please keep designs very simple.
• Examples:
• https://www.quolbin.com/install
• http://www.ventrohax.com/company/about-us
• http://brindlequota.org/
• http://www.trosk.com/
Should not have
• Minimal or no use of shadows and gradients

```html
<!DOCTYPE html>
<html lang="en">
<head>
<meta charset="utf-8">
<title>Harlow Clinics</title>
<link href="https://fonts.googleapis.com/css2?family=Raleway:wght@300;400;500;600&family=Ubuntu:wght@400;500&display=swap" rel="stylesheet">
<style>
:root{
  --ink:#1f1f1f;
  --muted:#555;
  --blue:#0f6ea9;
  --footer:#0c6aa7;
  --nav:#2b2b2b;
  --bar:#111;
  --rule:#e2e2e2;
}
*{box-sizing:border-box;margin:0;padding:0}
html,body{width:926px;height:1200px;overflow:hidden;background:#fff}
body{position:relative;font-family:"Raleway",sans-serif;color:var(--ink)}
a{color:inherit;text-decoration:none}
.abs{position:absolute}
.top-bar{left:0;top:0;width:926px;height:3px;background:var(--ink)}
.brand{left:116px;top:36px;display:flex;align-items:center;gap:11px}
.brand-square{width:43px;height:43px;background:#3a3a3a}
.brand-name{font-family:"Ubuntu",sans-serif;font-size:21px;color:#333}
.account{top:49px;right:116px;display:flex;gap:14px;font-size:12px;font-weight:500;color:#222}
.account span{display:flex;align-items:center;gap:6px}
.main-nav{left:116px;top:111px;width:694px;height:39px;background:var(--nav)}
.main-nav a{position:absolute;top:13px;color:#fff;font-size:11px;font-weight:500}
.hero{left:116px;top:150px;width:694px;height:256px;background:linear-gradient(100deg,#e6eef3 0%,#d4e2ea 45%,#8fc3e4 70%,#5aa6d6 100%)}
.hero-card{left:128px;top:229px;width:298px;height:99px;background:rgba(255,255,255,.9);padding:12px 20px}
.hero-card h1{font-family:"Ubuntu",sans-serif;font-weight:500;font-size:21px;color:#222}
.hero-card p{font-size:13.5px;color:var(--blue);margin-top:6px}
.dots{display:flex;gap:4px;margin-top:10px;margin-left:4px}
.dots i{width:7px;height:7px;border-radius:50%;background:#222}
.dots i:first-child{background:var(--blue)}
h2{font-weight:400;font-size:19px;color:#222}
.btn{display:inline-block;background:var(--blue);color:#fff;font-size:8px;font-weight:500;padding:0 10px;line-height:22px}
.about{left:116px;top:440px;width:240px}
.about .lead{font-size:10px;line-height:17px;margin-top:16px;color:#222}
.about .small{font-size:7.6px;line-height:14.5px;color:#444;margin-top:8px}
.about .btn{margin-top:14px}
.procedure{left:382px;top:442px;width:428px;height:168px;background:linear-gradient(180deg,#bfe2f7,#e3f3fc);border:1px solid #b5d8ee}
.procedure-photo{left:4px;top:14px;width:134px;height:153px;background:linear-gradient(180deg,#d8d2cd,#f2f2f2 60%,#e6e6e6)}
.procedure-body{left:153px;top:26px;width:250px}
.procedure-body p{font-size:9px;line-height:15.2px;color:#555;margin-top:14px}
.procedure-body .btn{margin-top:14px;font-size:8.5px;line-height:24px;padding:0 14px}
.divider{left:116px;top:644px;width:694px;height:1px;background:var(--rule)}
.col{top:676px}
.col .intro{font-size:9.8px;line-height:17px;margin-top:18px;color:#222}
.staff{left:116px;width:218px}
.staff .intro{text-align:justify}
.staff-card{display:flex;gap:13px;margin-top:12px}
.staff-photo{width:92px;height:74px;background:linear-gradient(135deg,#bcd8e8,#eef4f8);flex:none}
.staff-card .name{font-size:8.6px;color:var(--blue)}
.staff-card .role{font-size:8.2px;margin-top:4px}
.staff-card .desc{font-size:8px;color:#555;line-height:13.5px;margin-top:9px;text-align:justify}
.staff .btn{margin-top:14px}
.alerts{left:368px;width:204px}
.alerts .intro{text-align:justify}
.checklist{list-style:none;margin-top:9px}
.checklist li{display:flex;align-items:center;gap:13px;font-size:8.4px;color:#555;height:20px}
.checklist li.alert-new{color:var(--blue);font-weight:600}
.why{left:606px;width:200px}
.why .intro{font-size:9px;color:#555;line-height:16px}
.why .btn{margin-top:8px;width:104px;text-align:center;line-height:23px}
.why .second{margin-top:22px}
.footer-wave{left:0;top:900px;width:926px;height:252px}
.footer-col{top:978px;color:#fff}
.footer-col h3{font-weight:400;font-size:15px}
.footer-col ul{list-style:none;margin-top:12px}
.footer-col li{font-size:9.4px;line-height:15.2px}
.footer-col li.more{margin-top:4px;text-decoration:underline}
.contact-widget{left:696px;top:978px;width:114px;color:#fff}
.contact-widget h3{font-weight:400;font-size:15px}
.contact-list{list-style:none;margin-top:10px}
.contact-list li{display:flex;align-items:flex-start;gap:8px;font-size:9px;line-height:13px;margin-bottom:5px}
.contact-list svg{flex:none;margin-top:2px}
.contact-list li.directions{text-decoration:underline}
.bottom-bar{left:0;top:1152px;width:926px;height:48px;background:var(--bar);color:#aaa;font-size:8px}
.bottom-bar .legal{position:absolute;left:116px;top:20px;display:flex;gap:10px}
.bottom-bar .copy{position:absolute;right:114px;top:19px;font-size:8.4px}
</style>
</head>
<body>
<div class="abs top-bar"></div>

<header>
  <div class="abs brand"><span class="brand-square"></span><span class="brand-name">Harlow Clinics</span></div>
  <div class="abs account">
    <span><svg width="14" height="14" viewBox="0 0 14 14"><circle cx="5" cy="4" r="3" fill="var(--blue)"/><path d="M0 13c0-4 2-6 5-6s5 2 5 6z" fill="var(--blue)"/><circle cx="11" cy="10" r="2.6" fill="#fff" stroke="var(--blue)" stroke-width="1.2"/></svg>Login</span>
    <span><svg width="10" height="13" viewBox="0 0 10 13"><path d="M2.5 6V4a2.5 2.5 0 015 0v2" fill="none" stroke="var(--blue)" stroke-width="1.5"/><rect x="1" y="6" width="8" height="7" rx="1" fill="var(--blue)"/></svg>Signup</span>
  </div>
  <nav class="abs main-nav">
    <a style="left:33px">Home</a>
    <a style="left:114px">Clinic</a>
    <a style="left:192px">Our Staff</a>
    <a style="left:286px">Resources</a>
    <a style="left:390px">Contact us</a>
  </nav>
</header>

<section class="abs hero" role="img" aria-label="Photo of a smiling nurse in blue scrubs behind a grid of hexagons labelled with health topics"></section>
<div class="abs hero-card">
  <h1>Harlow Clinics</h1>
  <p>Lorem ipsum dolor sit amet consectetur</p>
  <div class="dots"><i></i><i></i><i></i></div>
</div>

<section class="abs about">
  <h2>About us</h2>
  <p class="lead">Lorem ipsum dolor sit amet, consectetur adipiscing elit, sed do eiusmod tempor incididunt</p>
  <p class="small">Lorem ipsum dolor sit amet, consectetur adipiscing elit, sed do eiusmod tempor incididunt ut labore et dolore magna aliqua. Ut enim ad minim veniam, quis nostrud exercitation ullamco laboris nisi ut aliquip ex ea commodo</p>
  <a class="btn">Read More about us</a>
</section>

<section class="abs procedure">
  <div class="abs procedure-photo" role="img" aria-label="Photo of a doctor in a white coat holding a clipboard"></div>
  <div class="abs procedure-body">
    <h2>Planning a Procedure ?</h2>
    <p>Lorem ipsum dolor sit amet, consectetur adipiscing elit, sed do eiusmod tempor incididunt ut labore et dolore magna aliqua. Ut enim ad</p>
    <a class="btn">Pre - Register Online &nbsp;&gt;</a>
  </div>
</section>

<div class="abs divider"></div>

<section class="abs col staff">
  <h2>Our staffs</h2>
  <p class="intro">Lorem ipsum dolor sit amet, consectetur adipiscing elit, sed do eiusmod</p>
  <div class="staff-card">
    <div class="staff-photo" role="img" aria-label="Photo of a staff doctor with a stethoscope"></div>
    <div>
      <div class="name">Ipsum Dolor</div>
      <div class="role">sit met adipiscing elit</div>
      <p class="desc">Lorem ipsum dolor sit amet, consecteturelit, sed do ipsum dolor</p>
    </div>
  </div>
  <a class="btn">Read More</a>
</section>

<section class="abs col alerts">
  <h2>Allerts &amp; bulletins</h2>
  <p class="intro">Lorem ipsum dolor sit amet, consectetur adipiscing elit, sed do eiusmod</p>
  <ul class="checklist">
    <li class="alert-new"><svg width="9" height="9" viewBox="0 0 10 10"><circle cx="5" cy="5" r="5" fill="var(--blue)"/><path d="M2.7 5.2l1.6 1.5 3-3.2" fill="none" stroke="#fff" stroke-width="1.3"/></svg>Now accepting new patients</li>
    <li><svg width="9" height="9" viewBox="0 0 10 10"><circle cx="5" cy="5" r="5" fill="var(--blue)"/><path d="M2.7 5.2l1.6 1.5 3-3.2" fill="none" stroke="#fff" stroke-width="1.3"/></svg>Consectetur adipiscing elit,</li>
    <li><svg width="9" height="9" viewBox="0 0 10 10"><circle cx="5" cy="5" r="5" fill="var(--blue)"/><path d="M2.7 5.2l1.6 1.5 3-3.2" fill="none" stroke="#fff" stroke-width="1.3"/></svg>Sed do eiusmod tempor</li>
    <li><svg width="9" height="9" viewBox="0 0 10 10"><circle cx="5" cy="5" r="5" fill="var(--blue)"/><path d="M2.7 5.2l1.6 1.5 3-3.2" fill="none" stroke="#fff" stroke-width="1.3"/></svg>Incididunt ut labore et dolore</li>
    <li><svg width="9" height="9" viewBox="0 0 10 10"><circle cx="5" cy="5" r="5" fill="var(--blue)"/><path d="M2.7 5.2l1.6 1.5 3-3.2" fill="none" stroke="#fff" stroke-width="1.3"/></svg>Magna aliqua. Ut enim</li>
    <li><svg width="9" height="9" viewBox="0 0 10 10"><circle cx="5" cy="5" r="5" fill="var(--blue)"/><path d="M2.7 5.2l1.6 1.5 3-3.2" fill="none" stroke="#fff" stroke-width="1.3"/></svg>Ad minim veniam, quis</li>
  </ul>
</section>

<section class="abs col why">
  <h2>Why we choose</h2>
  <p class="intro">Lorem ipsum dolor sit amet, consectetur adipi-scing elit, sed do eiusmod tempor</p>
  <a class="btn">Physician Toolbox</a>
  <p class="intro second">Lorem ipsum dolor sit amet, consectetur adipi-scing elit, sed do eiusmod</p>
  <a class="btn">Make an Appoinment</a>
</section>

<footer>
  <svg class="abs footer-wave" viewBox="0 0 926 252" preserveAspectRatio="none"><path d="M0 30 Q230 58 480 40 T926 12 L926 252 L0 252Z" fill="var(--footer)"/></svg>

  <div class="abs footer-col" style="left:116px">
    <h3>Patients &amp; Visitors</h3>
    <ul><li>Find a Doctor</li><li>Directions &amp; Parking</li><li>Information for Patients</li><li>Information for Visitors</li><li>Pay Hospital Bills Online</li><li>Financial Services</li><li>In the Neighborhood</li><li>Our Commitment to Quality</li></ul>
  </div>
  <div class="abs footer-col" style="left:306px">
    <h3>Clinic Policies</h3>
    <ul><li>Late Arrivals</li><li>Missed Appointments</li><li>Fees for Missed Appointments</li><li class="more">View all policies</li></ul>
  </div>
  <div class="abs footer-col" style="left:485px">
    <h3>Education &amp; Training</h3>
    <ul style="margin-top:9px"><li>Patient Health Library</li><li>Residency &amp; Fellowship</li><li>Information</li><li>Continuing Medical Education</li><li>Nursing Professional</li><li>Development</li><li>Allied &amp; Other Health</li></ul>
  </div>

  <div class="abs contact-widget">
    <h3>Contact &amp; Hours</h3>
    <ul class="contact-list">
      <li><svg width="9" height="9" viewBox="0 0 10 10"><circle cx="5" cy="5" r="4.3" fill="none" stroke="#fff" stroke-width="1.3"/><path d="M5 2.5V5l1.8 1.2" fill="none" stroke="#fff" stroke-width="1.2"/></svg>Mon–Fri 8am–6pm<br>Sat 9am–1pm</li>
      <li><svg width="9" height="9" viewBox="0 0 10 10"><path d="M2 0.5l2 2.2-1 1.3c.7 1.4 1.6 2.3 3 3l1.3-1 2.2 2-1.2 1.5C4.5 9.3.7 5.5.5 1.7z" fill="#fff"/></svg>Tel (555) 014-2290</li>
      <li><svg width="9" height="9" viewBox="0 0 10 10"><rect x="0.5" y="3" width="9" height="5.5" fill="none" stroke="#fff" stroke-width="1.2"/><rect x="2.5" y="0.5" width="5" height="3" fill="#fff"/></svg>Fax (555) 014-2291</li>
      <li><svg width="10" height="8" viewBox="0 0 10 8"><rect x="0.5" y="0.5" width="9" height="7" fill="none" stroke="#fff" stroke-width="1.1"/><path d="M0.8 1l4.2 3.3L9.2 1" fill="none" stroke="#fff" stroke-width="1.1"/></svg>info@harlowclinics.com</li>
      <li><svg width="8" height="10" viewBox="0 0 8 10"><path d="M4 10S0 5.8 0 3.8a4 4 0 018 0C8 5.8 4 10 4 10z" fill="#fff"/><circle cx="4" cy="3.8" r="1.4" fill="var(--footer)"/></svg>120 Alder Street,<br>Suite 4</li>
      <li class="directions"><svg width="9" height="9" viewBox="0 0 10 10"><path d="M1 5h7M5.5 2L8.5 5 5.5 8" fill="none" stroke="#fff" stroke-width="1.4"/></svg>Get directions</li>
    </ul>
  </div>

  <div class="abs bottom-bar">
    <div class="legal"><span>Privacy policy</span><span>Sitemap</span><span>Terms of use</span></div>
    <div class="copy">Copyrights @ 2015 Harlow Clinics. All Rights Reserved.</div>
  </div>
</footer>
</body>
</html>
```